The Neighbors Together Project

For submission to Lantern Campaign 2024
Need both Color and Black and White Versions
TITLE The Neighbors Together Project
Slogan; "Neighbors Together, one road...one Heart, just a different stride" -JT Pellow copyrights
Logo in Color and Logo in Black and White
Back of flyer will be The Field of Quiet Lanterns poem -JT Pellow
VOTE BLUE 2024 Header or Footer

I just want to thank you all for your participation in The Neighbors Together Project. In the next few days I will be reducing the choices down to 10. Id like for all of you to know Ive enjoyed seeing so many options and views on the Flyer. Mainly, I wanted to say to those who don't make the cut that I appreciate the work you've done.

LM Dorsey

```html
<!DOCTYPE html>
<html lang="en">
<head>
<meta charset="utf-8">
<title>The Neighbors Together Project — Flyer</title>
<link rel="stylesheet" href="https://fonts.googleapis.com/css2?family=Big+Shoulders+Stencil+Display:wght@800&family=Poppins:wght@400;500;600;700&family=Stardos+Stencil:wght@700&display=swap">
<style>
  :root {
    --backdrop: #a3a3a3;
    --paper: #eeeff1;
    --navy: #33355c;
    --slate: #3f5068;
    --brick: #b0463e;
    --ink: #262840;
    --illus-a: #4a4f7c;
    --illus-b: #b0463e;
    --illus-c: #d9a15a;
  }
  * { box-sizing: border-box; margin: 0; padding: 0; }
  html, body {
    width: 1200px; height: 800px; overflow: hidden;
    background: var(--backdrop);
    font-family: "Poppins", sans-serif;
  }
  .spread {
    position: relative; width: 1200px; height: 800px;
    display: flex; justify-content: center; align-items: center; gap: 44px;
  }
  .flyer {
    width: 440px; height: 590px;
    background: var(--paper);
    box-shadow: 0 10px 26px rgba(0,0,0,.22);
    padding: 30px 22px 28px;
    display: flex; flex-direction: column; align-items: center;
    text-align: center;
  }
  .rule-row {
    width: 100%; display: flex; align-items: center; gap: 12px;
  }
  .rule-row .line { flex: 1; height: 2px; background: var(--ink); }
  .rule-row .stars { flex: none; width: 34px; height: 34px; }
  .rule-row .label {
    font-weight: 700; font-size: 15px; letter-spacing: .32em;
    color: var(--ink); white-space: nowrap; padding-left: .32em;
  }
  .rule-row--top .stars { order: -1; }
  .rule-row--bottom .stars { order: 3; }

  /* front */
  .headline {
    margin-top: 38px;
    font-family: "Big Shoulders Stencil Display", sans-serif; font-weight: 800;
    font-size: 50px; line-height: 1; color: var(--slate);
    text-shadow: 2px 2px 0 var(--brick); letter-spacing: .01em;
    white-space: nowrap;
  }
  .subline {
    font-weight: 500; font-size: 22px; color: var(--brick);
    letter-spacing: .04em; line-height: 1.2; white-space: nowrap;
  }
  .headline + .subline { margin-top: 2px; }
  .illustration {
    margin: 14px 0 18px; width: 370px; height: 232px; border-radius: 4px;
    background: linear-gradient(135deg, var(--illus-a) 0%, var(--illus-a) 35%, var(--illus-b) 65%, var(--illus-c) 100%);
  }
  .closing {
    font-family: "Big Shoulders Stencil Display", sans-serif; font-weight: 800;
    font-size: 40px; line-height: 1.05; color: var(--slate);
    text-shadow: 2px 2px 0 var(--brick); margin-top: 2px; margin-bottom: auto;
    white-space: nowrap;
  }

  /* back */
  .poem-title {
    margin-top: 34px;
    font-family: "Stardos Stencil", serif; font-weight: 700;
    font-size: 23px; color: var(--brick); letter-spacing: .02em;
    white-space: nowrap;
  }
  .byline { font-size: 10px; font-weight: 500; color: var(--ink); margin-top: 2px; }
  .poem {
    margin-top: 22px;
    font-size: 10.5px; font-weight: 600; color: var(--ink); line-height: 1.65;
  }
  .poem p + p { margin-top: 12px; }
  .site {
    margin-top: auto; margin-bottom: 20px;
    font-size: 10px; font-weight: 500; color: var(--brick); letter-spacing: .04em;
  }
</style>
</head>
<body>
<svg width="0" height="0" style="position:absolute" aria-hidden="true">
  <defs>
    <symbol id="star-pair" viewBox="0 0 34 34">
      <polygon points="11,1 13.8,8.4 21.5,8.4 15.3,13 17.6,20.5 11,16 4.4,20.5 6.7,13 0.5,8.4 8.2,8.4" fill="#33355c"/>
      <polygon points="25,18 26.7,22.5 31.4,22.5 27.6,25.3 29,29.9 25,27.1 21,29.9 22.4,25.3 18.6,22.5 23.3,22.5" fill="#b0463e"/>
    </symbol>
  </defs>
</svg>

<main class="spread">
  <section class="flyer flyer--front">
    <div class="rule-row rule-row--top">
      <div class="line"></div>
      <span class="label">VOTE BLUE 2024</span>
      <div class="line"></div>
      <svg class="stars"><use href="#star-pair"/></svg>
    </div>

    <h1 class="headline">NEIGHBORS TOGETHER</h1>
    <p class="subline">ONE ROAD</p>
    <div class="illustration" role="img" aria-label="Illustration of a flag-patterned map with a row of diverse people holding hands in front of it"></div>
    <p class="subline">ONE HEART</p>
    <p class="closing">JUST A DIFFERENT STRIDE</p>

    <div class="rule-row rule-row--bottom">
      <svg class="stars"><use href="#star-pair"/></svg>
      <div class="line"></div>
      <span class="label">VOTE BLUE 2024</span>
      <div class="line"></div>
    </div>
  </section>

  <section class="flyer flyer--back">
    <div class="rule-row rule-row--top">
      <div class="line"></div>
      <span class="label">VOTE BLUE 2024</span>
      <div class="line"></div>
      <svg class="stars"><use href="#star-pair"/></svg>
    </div>

    <h2 class="poem-title">FIELD OF QUIET LANTERNS</h2>
    <p class="byline">By JT Pellow</p>

    <div class="poem">
      <p>Along the fence line, one by one,<br>small lights wake in the dusk.<br>No two burn quite the same shade,<br>yet every flame leans toward the road.</p>
      <p>A farmer's lamp, a student's jar,<br>a grandmother's tin with a dented lid,<br>carried out at evening<br>to keep a neighbor's gate in view.</p>
      <p>The wind comes low across the rows<br>and none of them goes dark,<br>because each one stands close enough<br>to borrow warmth from the next.</p>
      <p>So bring your light, however faint,<br>and set it where the path begins;<br>the field is wide, the night is long,<br>and there is room for all of us.</p>
    </div>

    <p class="site">WWW.NEIGHBORSTOGETHERPROJECT.COM</p>

    <div class="rule-row rule-row--bottom">
      <svg class="stars"><use href="#star-pair"/></svg>
      <div class="line"></div>
      <span class="label">VOTE BLUE 2024</span>
      <div class="line"></div>
    </div>
  </section>
</main>
</body>
</html>
```